Onboarding Infographic/brochure

We are a small criminal defense firm looking to create some sort of infographic or brochure that we can onboard new clients with. We are currently sending it out via email but want something a bit cooler and fun to send to clients. The information is:

A Few Quick Rules

We are here to help each step of the way. While questions are never discouraged, this letter will answer some of the most common ones we get asked.

Communications

As a client, you should always be in the loop. While we will try to respond to questions as quickly as possible, sometimes we are unable to respond right away. Do not worry - we promise to get back to you soon. Some questions might take some time to research, and a correct answer is better than a quick one.

Appointments

One of the benefits of having an attorney is the ability to discuss your case outside of court, minus the stress and headaches. If you need an appointment, please contact the office.

Appointments must be scheduled in advance. We do not want you to make a special trip to the office only to learn that we are in court or otherwise unavailable.

Jail Visits

If your family member is currently in jail, we take that very seriously. We will visit your loved one and introduce ourselves. While the case is ongoing, we ask that a family member be designated a “contact” person so that messages can be relayed quickly. Never discuss the facts of the case over the phone with someone who is in jail. Jail calls are recorded and we have seen too many cases go south based on remarks made over recorded lines.

Police Reports and Discovery

We will do our best to provide you with copies of everything we receive on your case. Most information will be emailed, so please keep your email address up to date.

Changes in Contact Information

If you move or change numbers during the case, please let us know. It is difficult to help if we are unable to reach you, and helping you is why we are here.

Court Appearances

Cases do not get resolved as quickly as they do on television. Expect there to be several hearings in your case and it may be necessary for you to attend one or more of them. If a hearing is set, you will receive notice of the date and time of each hearing.

Billing and Collections

We understand that this investment was a huge decision for you. As we focus on providing the best representation, we will need for you to stay on schedule with any payment arrangements agreed to at the time of your initial consultation.

Again, thank you for your trust in us. We look forward to getting a fantastic outcome on your case.

Target Market(s)

Criminal defense clients and their families

Industry/Entity Type

Legal

Font styles to use
Serif

Requirements
Must have
• Must incorporate all of the rules we email out. Would like diagrams, images or pictures
Nice to have
• We attached a Welcome brochure. Not sure I want it to look super similar, hence the request for infographic.

```html
<!DOCTYPE html>
<html lang="en">
<head>
<meta charset="UTF-8">
<title>Fidelis Defense Group – A Few Quick Rules</title>
<link href="https://fonts.googleapis.com/css2?family=Montserrat:wght@700&family=Bebas+Neue&family=Poppins:wght@300;400;500;600&display=swap" rel="stylesheet">
<style>
  :root {
    --ink: #111111;
    --royal: #004EAD;
    --sky: #0B98DE;
    --mist: #E8EFF8;
    --paper: #FFFFFF;
    --body-text: #1E2430;
  }
  * { box-sizing: border-box; margin: 0; padding: 0; }
  html, body { width: 848px; height: 1200px; overflow: hidden; background: var(--paper); }
  .sheet { width: 848px; height: 1200px; position: relative; font-family: "Poppins", sans-serif; }

  .masthead {
    height: 99px; display: flex; align-items: center; justify-content: center; gap: 14px;
  }
  .masthead .brand-mark { width: 26px; height: 26px; background: var(--sky); }
  .masthead .brand-name {
    font-family: "Montserrat", sans-serif; font-weight: 700; font-size: 42px;
    color: var(--ink); letter-spacing: 0.5px; line-height: 1;
  }

  .intro {
    height: 139px; background: var(--royal); color: var(--paper); text-align: center;
    padding-top: 22px;
  }
  .intro h1 { font-family: "Poppins", sans-serif; font-weight: 600; font-size: 38px; line-height: 1.1; letter-spacing: -0.3px; }
  .intro p { font-weight: 300; font-size: 17.5px; line-height: 24px; margin-top: 10px; }

  .rule { display: flex; position: relative; }
  .rule .label {
    width: 193px; flex: none; display: flex; flex-direction: column; align-items: center;
    justify-content: center; color: var(--paper); text-align: center; position: relative; gap: 10px;
  }
  .rule .label::after {
    content: ""; position: absolute; right: -12px; top: 50%; transform: translateY(-50%);
    border-top: 12px solid transparent; border-bottom: 12px solid transparent; border-left: 12px solid;
    border-left-color: inherit;
  }
  .rule h2 { font-family: "Bebas Neue", sans-serif; font-weight: 400; font-size: 21px; line-height: 24px; letter-spacing: 0.3px; }
  .rule .icon { width: 44px; height: 44px; }
  .rule .copy {
    flex: 1; display: flex; flex-direction: column; justify-content: center; gap: 8px;
    padding: 0 28px 0 31px; font-size: 13.4px; line-height: 19.2px; font-weight: 400; color: var(--body-text);
  }
  .rule.tone-sky .label { background: var(--sky); border-left-color: var(--sky); }
  .rule.tone-royal .label { background: var(--royal); border-left-color: var(--royal); }
  .rule.tone-sky .copy { background: var(--paper); }
  .rule.tone-royal .copy { background: var(--mist); }
  .justify { text-align: justify; }
</style>
</head>
<body>
<main class="sheet">
  <header class="masthead">
    <span class="brand-mark"></span>
    <span class="brand-name">FIDELIS DEFENSE GROUP</span>
  </header>

  <section class="intro">
    <h1>A Few Quick Rules</h1>
    <p>We are here to help each step of the way. While questions are never discouraged, this<br>letter will answer some of the most common ones we get asked.</p>
  </section>

  <article class="rule tone-sky" style="height:136px">
    <div class="label">
      <svg class="icon" viewBox="0 0 44 44" fill="#fff" aria-hidden="true">
        <rect x="5" y="2" width="20" height="16" rx="4"/>
        <path d="M11 18l-3 5 8-5z"/>
        <path d="M10 10l3 3 6-6" stroke="#0B98DE" stroke-width="2.4" fill="none" stroke-linecap="round"/>
        <path d="M28 5a7 7 0 0 1 0 13l3 5-7-5" stroke="#fff" stroke-width="3" fill="none"/>
        <circle cx="12" cy="28" r="4"/><path d="M4 42a8 8 0 0 1 16 0z"/>
        <circle cx="32" cy="28" r="4"/><path d="M24 42a8 8 0 0 1 16 0z"/>
      </svg>
      <h2>Communications</h2>
    </div>
    <div class="copy justify">
      <p>As a client, you should always be in the loop. While we will try to respond to questions as quickly as possible, sometimes we are unable to respond right away. Do not worry - we promise to get back to you soon. Some questions might take some time to research, and a correct answer is better than a quick one.</p>
    </div>
  </article>

  <article class="rule tone-royal" style="height:106px">
    <div class="label">
      <svg class="icon" viewBox="0 0 44 44" fill="#fff" aria-hidden="true">
        <rect x="4" y="7" width="30" height="28" rx="4"/>
        <rect x="10" y="3" width="3" height="7" rx="1.5"/><rect x="25" y="3" width="3" height="7" rx="1.5"/>
        <g fill="#004EAD"><rect x="8" y="16" width="5" height="5"/><rect x="16" y="16" width="5" height="5"/><rect x="24" y="16" width="5" height="5"/><rect x="8" y="25" width="5" height="5"/><rect x="16" y="25" width="5" height="5"/></g>
        <circle cx="34" cy="34" r="7" stroke="#004EAD" stroke-width="2"/>
        <path d="M30.5 34l2.5 2.5 4.5-4.5" stroke="#004EAD" stroke-width="2" fill="none"/>
      </svg>
      <h2>Appointments</h2>
    </div>
    <div class="copy">
      <p>One of the benefits of having an attorney is the ability to discuss your case outside of court, minus the stress and headaches. If you need an appointment, please contact the office. Appointments must be scheduled in advance. We do not want you to make a special trip to the office only to learn that we are in court or otherwise unavailable.</p>
    </div>
  </article>

  <article class="rule tone-sky" style="height:133px">
    <div class="label">
      <svg class="icon" viewBox="0 0 44 44" fill="none" stroke="#fff" stroke-width="2.6" aria-hidden="true">
        <rect x="6" y="4" width="32" height="36"/>
        <circle cx="22" cy="16" r="4.5" fill="#fff"/>
        <path d="M13 40v-8a9 7 0 0 1 18 0v8" fill="#fff"/>
        <line x1="12" y1="4" x2="12" y2="40"/><line x1="18" y1="4" x2="18" y2="40"/>
        <line x1="26" y1="4" x2="26" y2="40"/><line x1="32" y1="4" x2="32" y2="40"/>
      </svg>
      <h2>Jail Visits</h2>
    </div>
    <div class="copy justify">
      <p>If your family member is currently in jail, we take that very seriously. We will visit your loved one and introduce ourselves. While the case is ongoing, we ask that a family member be designated a “contact” person so that messages can be relayed quickly. Never discuss the facts of the case over the phone with someone who is in jail. Jail calls are recorded and we have seen too many cases go south based on remarks made over recorded lines.</p>
    </div>
  </article>

  <article class="rule tone-royal" style="height:139px">
    <div class="label">
      <svg class="icon" viewBox="0 0 44 44" fill="#fff" aria-hidden="true">
        <path d="M9 3h20l7 7v31H9z"/>
        <path d="M22 11l6 2v5c0 4-3 6-6 7-3-1-6-3-6-7v-5z" fill="none" stroke="#004EAD" stroke-width="2"/>
        <rect x="14" y="29" width="17" height="2" fill="#004EAD"/><rect x="14" y="34" width="17" height="2" fill="#004EAD"/>
      </svg>
      <h2>Police Reports<br>and Discovery</h2>
    </div>
    <div class="copy justify">
      <p>We will do our best to provide you with copies of everything we receive on your case. Most information will be emailed, so please keep your email address up to date.</p>
    </div>
  </article>

  <article class="rule tone-sky" style="height:155px">
    <div class="label">
      <svg class="icon" viewBox="0 0 44 44" fill="#fff" aria-hidden="true">
        <rect x="2" y="7" width="40" height="30" rx="4"/>
        <g fill="#0B98DE">
          <circle cx="13" cy="18" r="4"/><path d="M6 30a7 6 0 0 1 14 0z"/>
          <rect x="24" y="15" width="13" height="2.6"/><rect x="28" y="21" width="9" height="2.6"/><rect x="24" y="27" width="13" height="2.6"/>
        </g>
      </svg>
      <h2>Changes in<br>Contact Information</h2>
    </div>
    <div class="copy">
      <p>If you move or change numbers during the case, please let us know. It is difficult to help if we are unable to reach you, and helping you is why we are here.</p>
    </div>
  </article>

  <article class="rule tone-royal" style="height:124px">
    <div class="label">
      <svg class="icon" viewBox="0 0 44 44" fill="#fff" aria-hidden="true">
        <circle cx="10" cy="13" r="3"/><circle cx="22" cy="13" r="3"/><circle cx="34" cy="13" r="3"/>
        <path d="M4 22a6 5 0 0 1 12 0zM16 22a6 5 0 0 1 12 0zM28 22a6 5 0 0 1 12 0z"/>
        <path d="M16 4h12M22 2v6" stroke="#fff" stroke-width="1.6"/>
        <rect x="2" y="22" width="40" height="4"/>
        <rect x="6" y="26" width="32" height="11"/>
        <circle cx="22" cy="30" r="2.4" fill="#004EAD"/><path d="M17 36a5 4 0 0 1 10 0z" fill="#004EAD"/>
        <rect x="14" y="39" width="16" height="3"/>
      </svg>
      <h2>Court Appearances</h2>
    </div>
    <div class="copy justify">
      <p>Cases do not get resolved as quickly as they do on television. Expect there to be several hearings in your case and it may be necessary for you to attend one or more of them. If a hearing is set, you will receive notice of the date and time of each hearing.</p>
    </div>
  </article>

  <article class="rule tone-sky" style="height:169px">
    <div class="label">
      <svg class="icon" viewBox="0 0 44 44" fill="#fff" aria-hidden="true">
        <path d="M8 8h22v28a5 5 0 0 1-5 5H5a4 4 0 0 1-4-4h7z"/>
        <g fill="#0B98DE">
          <circle cx="13" cy="16" r="1.6"/><rect x="17" y="15" width="9" height="2"/>
          <circle cx="13" cy="23" r="1.6"/><rect x="17" y="22" width="9" height="2"/>
          <circle cx="13" cy="30" r="1.6"/><rect x="17" y="29" width="9" height="2"/>
        </g>
        <circle cx="34" cy="10" r="8" stroke="#0B98DE" stroke-width="1.5"/>
        <text x="34" y="14.5" font-family="Poppins, sans-serif" font-size="12" font-weight="600" text-anchor="middle" fill="#0B98DE">$</text>
      </svg>
      <h2>Billing and<br>Collections</h2>
    </div>
    <div class="copy justify">
      <p>We understand that this investment was a huge decision for you. As we focus on providing the best representation, we will need for you to stay on schedule with any payment arrangements agreed to at the time of your initial consultation.</p>
      <p>Again, thank you for your trust in us. We look forward to getting a fantastic outcome on your case.</p>
    </div>
  </article>
</main>
</body>
</html>
```